Website for legal expungement services with button to qualify/disqualify potential clients

Brightpath Record Renewal, LLC is a law firm focusing in legal expungement servcies (allowing people to erase criminal court records, police records, proseution files, etc). I want a more modern look which exudes confidence in the services. I am looking for a clean website that looks very polished. I want to keep the pages to a minimum, as I want the page not so much to answer questions, but to direct traffic to contact the law office. I would like the main focus point to be an button which would take a client through a series of questions to see if they would qualify for the services; this serves two purposes 1) to collect contact info for future marketing via email and 2) eliminate individuals who we are currently unable to help. A current theme that I have played around with are "Change so much, you'll need to reintroduce yourself" alongside a picture of a guys hand outstretched.
On the landing page, I would like a very brief and to the point explanation of what the service would be (i.e. "Leave your past in the past; expunge all your criminal records" ), followed by a list of benefits that it provides. (NB: included is a file "law post card-02" that includes the main benefits to expungement). Also included are two logo files for a more updated logo I currently use ("BRR Logo" and BRR Logo2") (NB: I'm open to revisions on this as well). Lastly, I've had two very minor 'ads' that I did ("postcard back" and "KVT Ad") that I like the idea of.

Target Market(s)

Middle/upper-middle class, mostly male, people with a criminal record or criminal accusation

Industry/Entity Type

Legal Services

Coding

Coded - Design and coding required

Requirements
Must have
• Button that attracts attention up front (possibly stand out coloring) to click to open up a series of questions to qualify/eliminate prospects, and simultaneously gather their info. Also, must be mobile friendly.

```html
<!DOCTYPE html>
<html lang="en">
<head>
<meta charset="utf-8">
<title>Brightpath Record Renewal</title>
<link href="https://fonts.googleapis.com/css2?family=Roboto:wght@400;500;700&display=swap" rel="stylesheet">
<style>
:root{
  --navy:#0b2f6b;
  --navy-deep:#072a63;
  --band:#153a78;
  --ink:#111;
  --white:#fff;
  --black:#000;
  --footer-brand:#0c2c66;
}
*{margin:0;padding:0;box-sizing:border-box}
html,body{width:1200px;height:3552px;overflow:hidden}
body{position:relative;background:var(--white);font-family:'Roboto',sans-serif;color:var(--ink)}
.abs{position:absolute}

/* header */
.site-header{left:0;top:0;width:1200px;height:105px;background:var(--white)}
.brand-box{left:108px;top:28px;width:100px;height:38px;border:2px solid var(--navy);color:var(--navy);font-size:24px;letter-spacing:8px;display:flex;align-items:center;justify-content:center;padding-left:8px}
.brand-divider{left:237px;top:8px;width:1px;height:76px;background:var(--navy)}
.brand-name{left:266px;top:33px;font-size:12px;line-height:13px;color:var(--navy);letter-spacing:.6px;text-transform:uppercase}
.main-nav a{position:absolute;top:40px;font-size:15px;font-weight:500;color:var(--navy);text-decoration:none}

/* hero */
.hero{left:0;top:105px;width:1200px;height:585px;background:linear-gradient(100deg,#1d2f6e 0%,#2a4d9a 45%,#6a7bb0 62%,#22357a 80%,#142766 100%)}
.hero-title{left:114px;top:258px;font-size:62px;line-height:69px;font-weight:500;color:var(--white)}
.hero-btn{left:111px;top:504px;width:334px;height:78px;background:var(--navy-deep);border:2px solid var(--white);color:var(--white);font-size:20px;font-weight:700;display:flex;align-items:center;justify-content:center}
.hero-arrow{width:30px;height:30px;border-radius:50%;background:var(--white)}

/* what we do */
.section-title{font-size:30px;font-weight:500;color:var(--ink)}
.intro-text{left:110px;top:842px;width:470px;font-size:20px;line-height:31px}
.btn-navy{background:var(--navy);color:var(--white);font-weight:700;font-size:20px;display:flex;align-items:center;justify-content:center;border-radius:6px}

.service-label{border:2px solid var(--navy);color:var(--navy);font-size:20px;font-weight:700;display:flex;align-items:center;justify-content:center;background:var(--white)}

/* case band */
.case-band{left:0;top:1696px;width:1200px;height:444px;background:linear-gradient(180deg,#1a3b78 0%,#14346f 60%,#0f2f68 100%)}
.case-title{left:0;top:1736px;width:1200px;text-align:center;font-size:30px;font-weight:500;color:var(--white)}
.case-num{width:50px;height:50px;border:2px solid var(--white);border-radius:50%;color:var(--white);font-size:19px;font-weight:700;display:flex;align-items:center;justify-content:center}
.case-text{font-size:20px;color:var(--white)}

/* benefits */
.benefit{width:214px;height:272px}
.benefit-text{left:0;width:214px;top:120px;text-align:center;font-size:20px;line-height:31px;padding:0 14px 0 20px}
.dot{width:12px;height:12px;border-radius:50%;border:1px solid #c8cfdc;top:2647px}

/* cta */
.cta-box{left:106px;top:2781px;width:988px;height:235px;background:var(--navy-deep);box-shadow:0 4px 8px rgba(0,0,0,.15)}
.cta-text{left:106px;top:2826px;width:988px;text-align:center;color:var(--white);font-size:31px;line-height:34px}
.cta-btn{left:530px;top:2929px;width:173px;height:53px;background:var(--white);color:var(--ink);border-radius:8px;font-size:20px;font-weight:700;display:flex;align-items:center;justify-content:center}

/* footer */
.site-footer{left:0;top:3101px;width:1200px;height:451px;background:var(--black)}
.footer-box{left:393px;top:3167px;width:134px;height:52px;border:2px solid var(--footer-brand);color:var(--footer-brand);font-size:32px;letter-spacing:12px;display:flex;align-items:center;justify-content:center;padding-left:12px}
.footer-divider{left:566px;top:3133px;width:1px;height:105px;background:var(--footer-brand)}
.footer-name{left:608px;top:3174px;font-size:22px;line-height:27px;color:var(--footer-brand);text-transform:uppercase;letter-spacing:.5px}
.footer-nav a{position:absolute;top:3284px;font-size:20px;font-weight:700;color:var(--white);text-decoration:none}
.contact-item{top:3366px;font-size:15px;color:var(--white);display:flex;align-items:center;gap:8px}
.social{width:30px;height:30px;border-radius:50%;background:var(--white);top:3430px}
.footer-rule{left:0;top:3504px;width:1200px;height:1px;background:#333}
.copyright{left:0;top:3518px;width:1200px;text-align:center;font-size:15px;color:var(--white)}
</style>
</head>
<body>

<header class="abs site-header">
  <div class="abs brand-box">BRR</div>
  <div class="abs brand-divider"></div>
  <div class="abs brand-name">Brightpath Record<br>Renewal</div>
  <nav class="main-nav">
    <a style="left:469px">HOME</a>
    <a style="left:565px">ABOUT US</a>
    <a style="left:692px">SERVICES</a>
    <a style="left:815px">BENEFITS OF EXPUNGING</a>
    <a style="left:1058px">CONTACT US</a>
  </nav>
</header>

<section class="abs hero" role="img" aria-label="Photo of a man in a suit extending his hand for a handshake"></section>
<h1 class="abs hero-title">Change so much,<br>you'll need to<br>reintroduce yourself</h1>
<div class="abs hero-btn">BOOK AN&nbsp; APPOINTMENT</div>
<svg class="abs hero-arrow" style="left:36px;top:346px" viewBox="0 0 30 30"><path d="M17 9 L11 15 L17 21" fill="none" stroke="#000" stroke-width="2.5"/></svg>
<svg class="abs hero-arrow" style="left:1130px;top:346px" viewBox="0 0 30 30"><path d="M13 9 L19 15 L13 21" fill="none" stroke="#000" stroke-width="2.5"/></svg>

<h2 class="abs section-title" style="left:113px;top:786px">WHAT WE DO</h2>
<p class="abs intro-text">Lorem ipsum dolor sit amet, consectetur adipiscing elit, sed do eiusmod tempor incididunt ut labore et dolore magna aliqua. Ut enim ad minim veniam, quis nostrud exercitation ullamco laboris nisi ut aliquip ex ea commodo consequat.</p>
<div class="abs btn-navy" style="left:109px;top:1015px;width:173px;height:53px">READ MORE</div>
<svg class="abs" style="left:665px;top:787px" width="429" height="280" role="img" aria-label="Photo of a lawyer reviewing a document with a client at a desk">
  <defs><linearGradient id="deskShade" x1="0" y1="0" x2="1" y2="1"><stop offset="0" stop-color="#3a3d44"/><stop offset=".5" stop-color="#8a8c92"/><stop offset="1" stop-color="#2b2d32"/></linearGradient></defs>
  <path d="M0 0 H429 V270 Q330 290 230 270 Q110 248 0 265 Z" fill="url(#deskShade)"/>
</svg>

<h2 class="abs section-title" style="left:0;width:1220px;text-align:center;top:1191px">OUR SERVICES</h2>
<svg class="abs" style="left:120px;top:1256px" width="467" height="272" role="img" aria-label="Photo of business people shaking hands in a meeting"><defs><linearGradient id="svcA" x1="0" y1="0" x2="1" y2="1"><stop offset="0" stop-color="#4d5560"/><stop offset="1" stop-color="#1f2a3c"/></linearGradient></defs><path d="M25 0 H467 V272 H0 V25 Q0 0 25 0 Z" fill="url(#svcA)"/></svg>
<div class="abs service-label" style="left:118px;top:1530px;width:471px;height:71px">LEAVE YOUR PAST IN THE PAST</div>
<div class="abs" style="left:626px;top:1260px;width:468px;height:272px;background:linear-gradient(135deg,#8c8f93,#55585c)" role="img" aria-label="Photo of an investigation desk with files, photos and a magnifying glass"></div>
<div class="abs service-label" style="left:625px;top:1535px;width:471px;height:71px">EXPUNGE ALL YOUR CRIMINAL RECORDS</div>

<section class="abs case-band" role="img" aria-label="Dim photo of a law library bookshelf in navy tones"></section>
<h2 class="abs case-title">TYPES OF CASE QUALITY</h2>
<div class="abs case-num" style="left:399px;top:1841px">01</div>
<div class="abs case-text" style="left:474px;top:1852px">Criminal accusation that were dismissed</div>
<div class="abs case-num" style="left:399px;top:1927px">02</div>
<div class="abs case-text" style="left:480px;top:1943px">Criminal cases&nbsp; that wen into diversionary program</div>
<div class="abs case-num" style="left:399px;top:2013px">03</div>
<div class="abs case-text" style="left:485px;top:2029px">Convictions</div>

<h2 class="abs section-title" style="left:0;width:1200px;text-align:center;top:2243px">BENEFITS OF EXPUNGING</h2>

<svg width="0" height="0" class="abs"><defs>
  <filter id="cardShadow" x="-10%" y="-10%" width="130%" height="130%"><feDropShadow dx="3" dy="3" stdDeviation="3" flood-opacity=".35"/></filter>
  <symbol id="cardShape" viewBox="0 0 214 272">
    <path d="M12 72 L115 18 L208 80 V266 H12 Z" fill="#fff" filter="url(#cardShadow)"/>
    <path d="M6 266 V75 Q6 52 70 40" fill="none" stroke="#0b2f6b" stroke-width="10"/>
    <circle cx="115" cy="44" r="44" fill="#0b2f6b"/>
  </symbol>
</defs></svg>

<div class="abs benefit" style="left:118px;top:2340px">
  <svg class="abs" width="214" height="272"><use href="#cardShape"/>
    <g fill="none" stroke="#fff" stroke-width="2.5"><rect x="101" y="30" width="28" height="20" rx="3"/><path d="M109 30 V25 H121 V30"/><path d="M92 58 Q104 52 116 58 H134 Q138 62 132 64 L112 70 Q100 70 92 66"/></g></svg>
  <p class="abs benefit-text">More and beter job opportunities leading to higher income</p>
</div>
<div class="abs benefit" style="left:367px;top:2340px">
  <svg class="abs" width="214" height="272"><use href="#cardShape"/>
    <g fill="none" stroke="#fff" stroke-width="2.5"><circle cx="115" cy="42" r="14"/><path d="M118 34 H112 Q108 34 108 38 Q108 42 115 42 Q122 42 122 46 Q122 50 118 50 H111 M115 30 V54"/><path d="M95 60 Q115 72 135 60"/></g></svg>
  <p class="abs benefit-text">Loan qualification and better loan rates</p>
</div>
<div class="abs benefit" style="left:616px;top:2340px">
  <svg class="abs" width="214" height="272"><use href="#cardShape"/>
    <g fill="none" stroke="#fff" stroke-width="2.5"><rect x="96" y="26" width="30" height="36" rx="2"/><path d="M101 34 H120 M101 41 H116 M101 48 H112"/><rect x="118" y="48" width="16" height="14" rx="2"/><path d="M121 48 V44 Q126 38 131 44 V48"/></g></svg>
  <p class="abs benefit-text">Protecting your privacy</p>
</div>
<div class="abs benefit" style="left:872px;top:2340px">
  <svg class="abs" width="214" height="272"><use href="#cardShape"/>
    <g fill="none" stroke="#fff" stroke-width="2.5"><path d="M91 38 L115 28 L139 38 L115 48 Z"/><path d="M101 42 V54 Q115 62 129 54 V42"/><path d="M139 38 V52"/></g></svg>
  <p class="abs benefit-text">Better education opportunities</p>
</div>
<div class="abs dot" style="left:569px;background:var(--navy);border-color:var(--navy)"></div>
<div class="abs dot" style="left:587px"></div>
<div class="abs dot" style="left:605px"></div>

<div class="abs cta-box"></div>
<p class="abs cta-text">To see if you quality for expungement&nbsp; or foe additional<br>information contact us</p>
<div class="abs cta-btn">CONTACT US</div>

<footer class="abs site-footer"></footer>
<div class="abs footer-box">BRR</div>
<div class="abs footer-divider"></div>
<div class="abs footer-name">Brightpath Record<br>Renewal</div>
<nav class="footer-nav">
  <a style="left:190px">HOME</a>
  <a style="left:313px">ABOUT US</a>
  <a style="left:477px">SERVICES</a>
  <a style="left:636px">BENEFITS OF EXPUNGING</a>
  <a style="left:953px">CONTACT US</a>
</nav>
<div class="abs contact-item" style="left:129px">
  <svg width="16" height="20" viewBox="0 0 16 20"><path d="M8 1 Q15 1 15 8 Q15 12 8 19 Q1 12 1 8 Q1 1 8 1 Z" fill="#fff"/><circle cx="8" cy="8" r="3" fill="#000"/></svg>
  14 Cedar Row ,Mn -870021</div>
<div class="abs contact-item" style="left:492px">
  <svg width="20" height="20" viewBox="0 0 20 20"><path d="M4 2 L8 2 L9 7 L6 9 Q8 13 11 14 L13 11 L18 12 L18 16 Q17 18 14 18 Q2 14 2 4 Q2 2 4 2 Z" fill="#fff"/></svg>
  555 - 010 - 0142</div>
<div class="abs contact-item" style="left:803px;top:3363px">
  <svg width="18" height="16" viewBox="0 0 18 16"><rect x="1" y="2" width="16" height="12" fill="none" stroke="#fff" stroke-width="1.5"/><path d="M1 2 L9 9 L17 2" fill="none" stroke="#fff" stroke-width="1.5"/></svg>
  info@brightpathrenewal.example</div>
<div class="abs social" style="left:500px"></div>
<div class="abs social" style="left:539px"></div>
<div class="abs social" style="left:580px"></div>
<div class="abs social" style="left:620px"></div>
<div class="abs footer-rule"></div>
<p class="abs copyright">Copyright © 2023 brightpath record renewal.All Rights Reserved</p>

</body>
</html>
```